sydney wedding photography business needs a business card design

we need a business card design for a sydney based wedding photography and videography business. our business name is :golden hour studio and film. our target clients are 24-35 yrs female. our style is candid, organic, natural, dynamic. we are a team of young photographers and videographers, and help brides to create memories that they will cherish for the rest of their lives. the logo will be provided. we want an elegant design that reflects our style, and also want to give a great impression to our clients that we are one of the best studios in sydney and our brand means quality and premium service.

Target Market(s)

bride to be, 24-35 years old, living in sydney and surrunding areas

Industry/Entity Type

Wedding Photography

Contact Information for Business Card

address: 57 tarrant street, glenmore nsw 2047
mobile: 0431872259
phone: (02) 9163 2408
info@tidewillowstudio.net.au
www.tidewillowstudio.net.au
facebook:tidewillowweddings
instagram:tidewillowweddings

Font styles to use
Serif
Sans Serif

Requirements
Nice to have
• maybe add my slogan"memories beyond eternity" if the layout looks good
Should not have
• no black color, not good idea for wedding biz card

```html
<!DOCTYPE html>
<html lang="en">
<head>
<meta charset="utf-8">
<title>Golden Hour Studio and Film – Business Card</title>
<link rel="stylesheet" href="https://fonts.googleapis.com/css2?family=Josefin+Sans:wght@600&family=Arimo:wght@400&display=swap">
<style>
  :root {
    --backdrop: #d8d2c8;
    --card: #3b2d23;
    --gold: #e8bf2a;
    --gold-stripe: #f0c623;
    --ink: #fbf6ee;
    --icon-ink: #3b2d23;
  }
  * { box-sizing: border-box; margin: 0; padding: 0; }
  html, body { width: 1200px; height: 922px; overflow: hidden; }
  body {
    background: var(--backdrop);
    display: flex;
    flex-direction: column;
    align-items: center;
    justify-content: center;
    gap: 40px;
  }
  .card {
    position: relative;
    width: 680px;
    height: 415px;
    background: var(--card);
    border-radius: 16px;
    overflow: hidden;
  }

  /* Brand name lockup */
  .brand {
    font-family: "Josefin Sans", sans-serif;
    font-weight: 600;
    color: var(--gold);
    text-transform: uppercase;
    text-align: center;
    line-height: 1;
  }
  .brand-name { display: block; }
  .brand-tag { display: block; }

  .card-front .brand {
    position: absolute;
    left: 0; right: 0; top: 50%;
    transform: translateY(-50%);
  }
  .card-front .brand-name { font-size: 62px; letter-spacing: 2px; }
  .card-front .brand-tag { font-size: 24px; letter-spacing: 12px; margin-top: 14px; }

  /* Back side */
  .photo-panel {
    position: absolute;
    left: 0; top: 0;
    width: 680px; height: 415px;
  }
  .card-back .brand {
    position: absolute;
    right: 28px; top: 62px;
    width: 300px;
  }
  .card-back .brand-name { font-size: 34px; letter-spacing: 1px; }
  .card-back .brand-tag { font-size: 13px; letter-spacing: 6px; margin-top: 8px; }

  .contact-list {
    position: absolute;
    right: 26px; bottom: 20px;
    list-style: none;
    font-family: "Arimo", sans-serif;
    font-size: 15px;
    color: var(--ink);
  }
  .contact-item {
    display: flex;
    align-items: center;
    justify-content: flex-end;
    gap: 10px;
    height: 24px;
    white-space: nowrap;
  }
  .contact-icon {
    width: 18px; height: 18px;
    background: var(--gold);
    border-radius: 2px;
    flex: none;
  }
  .contact-icon svg { display: block; width: 18px; height: 18px; }
</style>
</head>
<body>

  <section class="card card-front" aria-label="Business card front">
    <div class="brand">
      <span class="brand-name">Golden Hour</span>
      <span class="brand-tag">Studio and Film</span>
    </div>
  </section>

  <section class="card card-back" aria-label="Business card back">
    <svg class="photo-panel" viewBox="0 0 680 415">
      <defs>
        <linearGradient id="sunset" x1="0" y1="0" x2="0.3" y2="1">
          <stop offset="0" stop-color="#e7c9a0"/>
          <stop offset="0.3" stop-color="#9a7a55"/>
          <stop offset="0.65" stop-color="#4a3a2a"/>
          <stop offset="1" stop-color="#c9b7a8"/>
        </linearGradient>
      </defs>
      <path role="img" aria-label="Photo of a bride and groom embracing at sunset beside a rustic wooden fence"
            d="M0 0 H330 C300 170 262 320 200 415 H0 Z" fill="url(#sunset)"/>
      <path class="gold-stripe" d="M330 0 H342 C316 180 282 330 228 415 H200 C262 320 300 170 330 0 Z" fill="var(--gold-stripe)"/>
    </svg>

    <div class="brand">
      <span class="brand-name">Golden Hour</span>
      <span class="brand-tag">Studio and Film</span>
    </div>

    <ul class="contact-list">
      <li class="contact-item">(02) 9163 2408
        <span class="contact-icon"><svg viewBox="0 0 17 17"><path d="M5 3.5 L7 6 L6 7.3 C6.8 9 8 10.2 9.7 11 L11 10 L13.5 12 L12.3 13.6 C8 13.4 3.6 9 3.4 4.7 Z" fill="var(--icon-ink)"/></svg></span></li>
      <li class="contact-item">0431872259
        <span class="contact-icon"><svg viewBox="0 0 17 17"><rect x="5.5" y="3" width="6" height="11" rx="1" fill="none" stroke="var(--icon-ink)" stroke-width="1.4"/><circle cx="8.5" cy="12" r="0.8" fill="var(--icon-ink)"/></svg></span></li>
      <li class="contact-item">www.tidewillowstudio.net.au
        <span class="contact-icon"><svg viewBox="0 0 17 17"><circle cx="8.5" cy="8.5" r="5" fill="none" stroke="var(--icon-ink)" stroke-width="1.3"/><ellipse cx="8.5" cy="8.5" rx="2.2" ry="5" fill="none" stroke="var(--icon-ink)" stroke-width="1"/><path d="M3.5 8.5 H13.5" stroke="var(--icon-ink)" stroke-width="1"/></svg></span></li>
      <li class="contact-item">info@tidewillowstudio.net.au
        <span class="contact-icon"><svg viewBox="0 0 17 17"><rect x="3" y="5" width="11" height="7.5" fill="none" stroke="var(--icon-ink)" stroke-width="1.3"/><path d="M3 5 L8.5 9.5 L14 5" fill="none" stroke="var(--icon-ink)" stroke-width="1.3"/></svg></span></li>
      <li class="contact-item">tidewillowweddings
        <span class="contact-icon"><svg viewBox="0 0 17 17"><circle cx="8.5" cy="8.5" r="2" fill="none" stroke="var(--icon-ink)" stroke-width="1.3"/><path d="M10.5 6.5 V9.6 C10.5 11.2 13.3 11.2 13.3 8.5 A4.8 4.8 0 1 0 11 12.6" fill="none" stroke="var(--icon-ink)" stroke-width="1.3"/></svg></span></li>
      <li class="contact-item">tidewillowweddings
        <span class="contact-icon"><svg viewBox="0 0 17 17"><path d="M3.5 4.5 H13.5 V11 H8 L5.3 13.4 V11 H3.5 Z" fill="none" stroke="var(--icon-ink)" stroke-width="1.3" stroke-linejoin="round"/></svg></span></li>
      <li class="contact-item">57 tarrant street, glenmore nsw 2047
        <span class="contact-icon"><svg viewBox="0 0 17 17"><path d="M8.5 14 C5.5 10.5 4.5 8.5 4.5 7 A4 4 0 0 1 12.5 7 C12.5 8.5 11.5 10.5 8.5 14 Z" fill="var(--icon-ink)"/><circle cx="8.5" cy="7" r="1.5" fill="var(--gold)"/></svg></span></li>
    </ul>
  </section>

</body>
</html>
```